Corporate Business Card

Very professional, Modern, Not to busy, include phone address email, website
(253) 617-4930, 18761 52nd Avenue S, Kent, WA 98047, martin@plumlinegroup.com, varkoworks.com

Target Market(s)

Manufacturing

Industry/Entity Type

Aero, machining, manufacturing, Off road racing

Contact Information for Business Card

Phone, address email, website

```html
<!DOCTYPE html>
<html lang="en">
<head>
<meta charset="utf-8">
<title>Varko Works – Business Card</title>
<link href="https://fonts.googleapis.com/css2?family=Roboto:wght@400;700;900&display=swap" rel="stylesheet">
<style>
  :root {
    --navy: #13296b;
    --navy-deep: #0a1a4f;
    --navy-light: #1b3a8a;
    --red: #d8232a;
    --white: #ffffff;
    --stage: #e4e5e8;
  }
  * { margin: 0; padding: 0; box-sizing: border-box; }
  html, body {
    width: 1200px; height: 800px; overflow: hidden;
    background: var(--stage);
    font-family: "Roboto", Arial, sans-serif;
  }
  .sheet {
    width: 1200px; height: 800px;
    display: flex; align-items: center; justify-content: center; gap: 60px;
  }
  .card {
    position: relative;
    width: 525px; height: 300px;
    border-radius: 4px;
    overflow: hidden;
    box-shadow: 0 10px 28px rgba(0,0,0,0.16);
  }

  /* Front */
  .card--front {
    background: radial-gradient(ellipse at 55% 35%, var(--navy-light) 0%, var(--navy) 45%, var(--navy-deep) 100%);
    display: flex; align-items: center; justify-content: center;
  }
  .brand {
    display: flex; align-items: center; gap: 12px;
    font-weight: 900; letter-spacing: 1px; text-transform: uppercase;
  }
  .brand__mark { width: 22px; height: 22px; background: var(--red); }
  .card--front .brand__name { color: var(--white); font-size: 46px; }

  /* Back */
  .card--back { background: var(--white); }
  .card--back .brand { position: absolute; top: 42px; right: 44px; }
  .card--back .brand__name { color: var(--navy); font-size: 40px; }
  .card--back .brand__mark { width: 18px; height: 18px; }

  .accent-line {
    position: absolute; left: 0; right: 0; bottom: 78px;
    height: 6px; background: var(--navy);
  }
  .web-band {
    position: absolute; left: 0; right: 0; bottom: 0; height: 66px;
    background: var(--red);
    display: flex; align-items: center; justify-content: flex-end;
    padding-right: 34px;
  }
  .web-band__url { color: var(--white); font-size: 15px; letter-spacing: 1px; }

  .contact-panel {
    position: absolute; left: 0; bottom: 0;
    width: 250px; height: 138px;
    background: linear-gradient(135deg, var(--navy-light), var(--navy-deep));
    border-top-right-radius: 18px;
    padding: 22px 16px 0 20px;
    list-style: none;
  }
  .contact-panel li {
    display: flex; align-items: center; gap: 8px;
    color: var(--white); font-size: 13px; line-height: 1.2;
    margin-bottom: 11px;
  }
  .contact-panel svg { width: 12px; height: 12px; flex: none; fill: var(--red); }
</style>
</head>
<body>
<main class="sheet">
  <section class="card card--front" aria-label="Card front">
    <div class="brand">
      <span class="brand__mark"></span>
      <span class="brand__name">Varko Works</span>
    </div>
  </section>

  <section class="card card--back" aria-label="Card back">
    <div class="brand">
      <span class="brand__mark"></span>
      <span class="brand__name">Varko Works</span>
    </div>

    <div class="accent-line"></div>
    <div class="web-band"><span class="web-band__url">www.varkoworks.com</span></div>

    <ul class="contact-panel">
      <li>
        <svg viewBox="0 0 24 24" aria-hidden="true"><path d="M6.6 10.8a15.2 15.2 0 0 0 6.6 6.6l2.2-2.2c.3-.3.7-.4 1-.2 1.1.4 2.3.6 3.6.6.6 0 1 .4 1 1V20c0 .6-.4 1-1 1A17 17 0 0 1 3 4c0-.6.4-1 1-1h3.5c.6 0 1 .4 1 1 0 1.3.2 2.5.6 3.6.1.3 0 .7-.2 1z"/></svg>
        <span>(253) 617-4930</span>
      </li>
      <li>
        <svg viewBox="0 0 24 24" aria-hidden="true"><path d="M2 5h20v14H2z M2 5l10 8 10-8" /></svg>
        <span>martin@plumlinegroup.com</span>
      </li>
      <li>
        <svg viewBox="0 0 24 24" aria-hidden="true"><path d="M12 2a7 7 0 0 0-7 7c0 5.2 7 13 7 13s7-7.8 7-13a7 7 0 0 0-7-7zm0 9.5a2.5 2.5 0 1 1 0-5 2.5 2.5 0 0 1 0 5z"/></svg>
        <span>18761 52nd Avenue S, Kent, WA 98047</span>
      </li>
    </ul>
  </section>
</main>
</body>
</html>
```